3 Business Card designs for a company with multiple services

We are a company that has 3 main services:

1) Security - CCTV & Alarm Sepcialists
2) Broadcast - Broadcast Sales and Technical Services
3) Distribution - Quality Products, Quality Service

The broadcast service is for Video Broadcast.

I will include our logos for each service.

I would like to also create a business card design for 7QR in general (see main logo).

Each card will be two-sided. On the front I would think it would include Logo, Name, Posistion and Mobile (and possibly email). And possibly our main number (which may be something like 1800 639 415)

On the back it MUST include a "lined" section to be able to write short quotes / prices.

Then include more details like Phone: 1800 639 415 Fax: 1800 639 417 Postal: PO Box 917, Tallowfield, QLD Australia 4287 Website: www.7qr.com.au

We would like a fresh, inovative card design with that "wow check this out" feel about it.

Look forward to seeing what you can do! :)

Corin

• Quote section on the back!
Editable files.

```html
<!DOCTYPE html>
<html lang="en">
<head>
<meta charset="utf-8">
<title>7QR – Business Card</title>
<link rel="stylesheet" href="https://fonts.googleapis.com/css2?family=Arimo:wght@400&display=swap">
<style>
  :root {
    --navy-deep: #041566;
    --navy: #0a2a8f;
    --royal: #0a3aa6;
    --cyan-glow: #1f86c6;
    --rule-blue: #5cb8ee;
    --text-white: #ffffff;
    --text-soft: #cfd9ec;
  }
  html, body {
    margin: 0;
    padding: 0;
    width: 1200px;
    height: 721px;
    overflow: hidden;
    background: var(--navy-deep);
  }
  .card {
    position: relative;
    width: 1200px;
    height: 721px;
    overflow: hidden;
    font-family: "Arimo", Arial, sans-serif;
    background:
      radial-gradient(ellipse 620px 520px at 430px 380px, var(--cyan-glow) 0%, #1560b0 35%, var(--navy) 70%, var(--navy-deep) 100%);
  }
  .card__backdrop {
    position: absolute;
    inset: 0;
  }
  .card__art {
    position: absolute;
    left: 120px;
    top: 120px;
    width: 620px;
    height: 520px;
    border-radius: 50%;
    background: radial-gradient(closest-side, rgba(120, 200, 235, 0.28), rgba(120, 200, 235, 0) 100%);
  }
  .brand {
    position: absolute;
    right: 187px;
    top: 270px;
    margin: 0;
    color: var(--text-white);
    font-size: 72px;
    font-weight: 400;
    letter-spacing: 4px;
    line-height: 1;
    text-align: right;
  }
  .contact {
    position: absolute;
    right: 187px;
    top: 460px;
    width: 600px;
    text-align: right;
  }
  .contact__name {
    margin: 0;
    color: var(--text-white);
    font-size: 33px;
    font-weight: 400;
    letter-spacing: -0.5px;
    line-height: 40px;
  }
  .contact__rule {
    width: 565px;
    height: 2px;
    margin: 13px 0 9px auto;
    background: var(--rule-blue);
    border: 0;
  }
  .contact__details {
    margin: 0;
    color: var(--text-soft);
    font-size: 22px;
    letter-spacing: 1.2px;
    line-height: 26.5px;
  }
</style>
</head>
<body>
  <main class="card">
    <svg class="card__backdrop" width="1200" height="721" viewBox="0 0 1200 721" aria-hidden="true">
      <polygon points="50,13 64,0 704,0 743,55 334,375" fill="var(--royal)"/>
      <polygon points="725,0 1170,0 890,216" fill="var(--royal)"/>
    </svg>
    <div class="card__art" role="img" aria-label="Soft abstract feather and swirl artwork in pale blue"></div>

    <p class="brand">7QR</p>

    <section class="contact">
      <h1 class="contact__name">LOREM IPSUM DOLOR</h1>
      <hr class="contact__rule">
      <p class="contact__details">
        Manager<br>
        123.4567.890 ||| 1800 639 415<br>
        LoremIpsumDolor@7qr.com
      </p>
    </section>
  </main>
</body>
</html>
```